QRTV Membership Web Design Project

We need a website design for QRTV membership. We need something different from what we currently have. See what we currently have: http://www.qorvatu.org/klt4/

Make provision for where members bushiness can be advertised.
Updates

We need a box for advertising members projects/business.

Make provision for where members bushiness / products can be advertised.

Target Market(s)

For members of QRTV and Intending members. Membership is for married men only.

Requirements
Must have
• Make provision for where members bushiness can be advertised.

You are to redesign: http://www.qorvatu.org/klt4/

```html
<!DOCTYPE html>
<html lang="en">
<head>
<meta charset="utf-8">
<title>QRTV – Quorum of Righteous Trust Vanguard</title>
<link rel="stylesheet" href="https://fonts.googleapis.com/css2?family=Arimo:ital,wght@0,400;0,700;1,700&display=swap">
<style>
:root{
  --header-bg:#ebe8e3;
  --page-bg:#f4f3f0;
  --text:#444;
  --heading:#4d4d4d;
  --muted:#555;
  --news-blue:#3e8fc5;
  --hero-dark:#0d0d0d;
  --btn-blue:#0f6e9a;
  --field:#b3ada5;
  --footer-bg:#b7b2aa;
  --footer-line:#8f8a83;
  --white:#fff;
}
*{margin:0;padding:0;box-sizing:border-box}
html,body{width:900px;height:1200px;overflow:hidden}
body{position:relative;background:var(--page-bg);font-family:Arimo,Arial,sans-serif;color:var(--text)}
.abs{position:absolute}
.site-header{left:0;top:0;width:900px;height:129px;background:var(--header-bg)}
.brand{left:18px;top:28px;display:flex;align-items:center;gap:10px}
.brand-mark{width:70px;height:70px;border-radius:50%;background:#2f6f9a}
.brand-name{font-size:22px;color:#3a4f6a;font-weight:400}
.tagline{left:100px;top:90px;font-size:15px;color:#5a5a5a;font-weight:400}
.search{left:737px;top:22px;display:flex}
.search-field{width:94px;height:21px;border:1px solid #bbb;border-radius:10px 0 0 10px;background:var(--white)}
.search-btn{width:46px;height:21px;border:1px solid #bbb;border-left:0;border-radius:0 10px 10px 0;background:linear-gradient(#f8f8f8,#dcdcdc);font-size:11px;color:#444;line-height:19px;text-align:center}
.main-nav{left:0;top:129px;width:900px;height:28px;background:linear-gradient(#fafafa,#e4e4e4);border-top:1px solid #ccc;border-bottom:1px solid #ccc;display:flex;padding-left:63px}
.main-nav a{font-size:12px;color:#444;text-decoration:none;line-height:26px;padding:0 9px;border-right:1px solid #d0d0d0}
.main-nav a.current{background:var(--white);padding:0 22px}
.hero{left:24px;top:157px;width:834px;height:244px;background:var(--hero-dark)}
.hero-photo{position:absolute;right:0;top:0;width:330px;height:244px;background:linear-gradient(90deg,#0d0d0d,#4a2f22 45%,#8a5e45)}
.hero-title{left:14px;top:72px;color:var(--white);font-size:22px;line-height:31px;font-weight:400}
.hero-btn{left:26px;top:172px;width:88px;height:25px;background:linear-gradient(#1a88b8,var(--btn-blue));border:1px solid #0a4f70;color:var(--white);font-size:12px;line-height:23px;text-align:center}
.products{left:26px;top:423px;width:488px;height:272px;background:var(--white);border:1px solid #ddd;border-radius:3px}
.section-title{font-size:18px;font-weight:700;color:#333}
.products .section-title{left:13px;top:8px}
.product{top:33px;width:222px}
.product-img{width:222px;height:88px;border:4px solid var(--white);outline:1px solid #ddd}
.product h3{font-size:14px;color:#555;margin:14px 8px 6px;font-weight:700}
.product p{font-size:8.6px;line-height:16.3px;text-align:justify;margin:0 8px;color:#555}
.btn{height:23px;padding:0 7px;border:1px solid #aaa;border-radius:3px;background:linear-gradient(#fdfcf7,#dedbcc);font-size:11px;color:#222;line-height:21px;text-align:center;box-shadow:0 1px 1px rgba(0,0,0,.15)}
.news-title{left:647px;top:438px;font-size:15px;font-weight:700;color:var(--news-blue)}
.news-item{left:576px;width:256px;font-size:8.6px;line-height:16.5px;color:#555;padding-bottom:8px;border-bottom:1px solid #e6e5e1}
.welcome-title{left:58px;top:728px;font-size:15.5px;font-weight:700;color:var(--heading)}
.welcome-img{left:42px;top:768px;width:106px;height:160px;border:4px solid var(--white);outline:1px solid #ddd;background:linear-gradient(#1a1a1a,#6b4632 50%,#1a1a1a)}
.welcome-text{left:158px;top:785px;width:308px;font-size:10.4px;line-height:15px;text-align:justify;color:#444}
.join-title{left:577px;top:715px;font-size:14px;font-weight:700;color:var(--heading)}
.field{left:577px;width:233px;background:var(--field);border:1px solid #8c877f;border-radius:2px;font-size:10.5px;color:#333;padding:12px 11px}
.site-footer{left:0;top:1004px;width:900px;height:196px;background:var(--footer-bg);border-top:1px solid #8a8680}
.newsletter-title{left:50px;top:28px;font-size:13.5px;font-weight:700;color:#444}
.newsletter-field{left:48px;top:52px;width:221px;height:24px;background:var(--white);border:1px solid #aaa;border-radius:2px;font-size:9.5px;font-weight:700;font-style:italic;color:#333;padding:6px 17px}
.social{left:710px;top:26px;display:flex;gap:3px}
.social span{width:36px;height:36px;border-radius:5px;background:#3d7bbf}
.footer-rule{left:36px;top:132px;width:830px;height:1px;background:var(--footer-line)}
.copyright{left:35px;top:148px;font-size:8px;color:var(--white)}
.footer-nav{left:427px;top:154px;display:flex}
.footer-nav a{font-size:8px;color:#444;text-decoration:none;margin-right:16px}
.page-code{left:874px;top:180px;font-size:11px;color:#222}
</style>
</head>
<body>
<header class="site-header abs">
  <div class="brand abs"><span class="brand-mark"></span><span class="brand-name">QRTV</span></div>
  <p class="tagline abs">Manifesting the Glory of God</p>
  <div class="search abs"><span class="search-field"></span><span class="search-btn">Search</span></div>
</header>

<nav class="main-nav abs">
  <a class="current" href="#">Home</a><a href="#">About Us</a><a href="#">Membership</a><a href="#">Membership Levels</a><a href="#">Membership Projects</a><a href="#">Links</a><a href="#" style="border:0">Contact Us</a>
</nav>

<section class="hero abs">
  <div class="hero-photo" role="img" aria-label="Man praying with hands clasped near his chin"></div>
  <h1 class="hero-title abs">Lorem ipsum dolor sit amet,<br>&nbsp;consectetur adipisicing elit,</h1>
  <div class="hero-btn abs">Learn More</div>
</section>

<section class="products abs">
  <h2 class="section-title abs">Products</h2>
  <article class="product abs" style="left:8px">
    <div class="product-img" role="img" aria-label="Open hands holding letter blocks spelling pray" style="background:linear-gradient(90deg,#d9a98e,#e8c2aa 50%,#c98f74)"></div>
    <h3>Lorem ipsum dolor sit amet</h3>
    <p>Lorem ipsum dolor sit amet, consectetur adipisic-ing elit, sed do eiusmod tempor incididunt ut labore et dolore magna aliqua. Ut enim ad minim veniam, quis nostrud exercitation ullamco laboris nisi ut aliquip ex ea commodo consequat.</p>
  </article>
  <article class="product abs" style="left:265px">
    <div class="product-img" role="img" aria-label="Congregation kneeling in prayer" style="background:linear-gradient(90deg,#2e2a35,#7a5a66 50%,#6a4a3e)"></div>
    <h3>Lorem ipsum dolor sit amet</h3>
    <p>Lorem ipsum dolor sit amet, consectetur adipisic-ing elit, sed do eiusmod tempor incididunt ut labore et dolore magna aliqua. Ut enim ad minim veniam, quis nostrud exercitation ullamco laboris nisi ut aliquip ex ea commodo consequat.</p>
  </article>
  <div class="btn abs" style="left:14px;top:240px">Read More</div>
  <div class="btn abs" style="left:256px;top:240px">Read More</div>
</section>

<h2 class="news-title abs">LATEST NEWS</h2>
<p class="news-item abs" style="top:486px">Lorem ipsum dolor sit amet, consectetur adipisicing elit, sed do eiusmod tempor incididunt ut labore et dolore magna aliqua.</p>
<p class="news-item abs" style="top:545px">Lorem ipsum dolor sit amet, consectetur adipisicing elit, sed do eiusmod tempor incididunt ut labore et dolore magna aliqua.</p>
<p class="news-item abs" style="top:600px;border:0">Lorem ipsum dolor sit amet, consectetur adipisicing elit, sed do eiusmod tempor incididunt ut labore et dolore magna aliqua.</p>
<div class="btn abs" style="left:748px;top:663px">Read More</div>

<h2 class="welcome-title abs">Welcome to &nbsp;Quorum of Righteous Trust Vanguard (QRTV)</h2>
<div class="welcome-img abs" role="img" aria-label="Hands clasped in prayer"></div>
<p class="welcome-text abs">Lorem ipsum dolor sit amet, consectetur adipisicing elit, sed do eiusmod tempor incididunt ut labore et dolore magna aliqua. Ut enim ad minim veniam, quis nostrud exercitation ullamco laboris nisi ut aliquip ex ea commodo consequat. Duis aute irure dolor in reprehenderit in voluptate velit esse cillum dolore eu fugiat nulla pariatur. Excepteur sint occaecat cupidatat non proident, sunt in culpa qui officia deserunt mollit anim id est laborum.</p>
<div class="btn abs" style="left:403px;top:920px">Read More</div>

<h2 class="join-title abs">Join Us</h2>
<div class="field abs" style="top:743px;height:34px">Name</div>
<div class="field abs" style="top:788px;height:34px">Email Id</div>
<div class="field abs" style="top:832px;height:83px;padding-top:8px">Message</div>
<div class="btn abs" style="left:746px;top:933px;width:66px">Submit</div>

<footer class="site-footer abs">
  <h2 class="newsletter-title abs">Subscribe to our Newsletter</h2>
  <div class="newsletter-field abs">Your Email Id</div>
  <div class="btn abs" style="left:190px;top:83px">Subscribe</div>
  <div class="social abs" aria-label="Social links"><span></span><span style="background:#4fb6e6"></span><span style="background:#2e7fb5"></span></div>
  <div class="footer-rule abs"></div>
  <p class="copyright abs">QUORUM OF RIGHTEOUS TRUST VANGUARD Copyright 2012. All rights reserved.</p>
  <nav class="footer-nav abs"><a href="#">Home</a><a href="#">About Us</a><a href="#">Membership</a><a href="#">Membership Levels</a><a href="#">Membership Projects</a><a href="#">Links</a><a href="#">Contact Us</a></nav>
  <span class="page-code abs">X32</span>
</footer>
</body>
</html>
```